Calendar Design Project: 2025 with Specific Edits

This is a straightforward project where your creativity can shine!
Simply take the existing 2024 calendar and adapt it for 2025 by incorporating the new photos I've attached.
Please keep the overall concept of the 2024 calendar intact—your focus will be on enhancing it with fresh visuals.

I can't wait to see your amazing designs!
I am looking for a talented graphic designer to create a new 2025 calendar with specific adjustments.
Pictures attached.
Requirements:
Calendar Size: 52cm x 34cm
March Folder:
Adjust the image named "attached - DJI-0025" to make the circular road darker to match the rest of the design.
May Folder:
Modify the circled area in the May image to ensure it looks consistent with the other road (reference file: "attached - After").
November Folder:
Clear out the circled area in the November image (reference file: "attached - After1").
Please let me know if you have any questions or need further clarification.
I added to my breif a design i made last year for same client.
2025, calendar should be vertical and not horizontal. and some of the photos attache are "Before" and "After" please include together inside each month of the calendar.
Thank you!
Feel free to adjust any details as necessary!

Hello talented designers!

I’m excited to share that this is my 14th project on the ArtHive platform, and I’ve been fortunate to have successful collaborations in the past. I'm looking forward to creating a new 2025 calendar with your help, and I believe that with your creativity and skills, we can make this project a success as well!

I hope to establish a long-term relationship with a talented team like yours. As an added incentive, I will be offering a bonus for the winner, and I may select more than one winner, so everyone has a chance to shine!

Let’s make something amazing together!

Best
Update:
cancel or before, only place the After picture

Requirements
Must have
• Project Overview Objective: Create a 2025 calendar using the provided images, maintaining the design concept from the 2024 calendar but enhancing it with new visuals. Format: Vertical layout (52cm x 34cm).

```html
<!DOCTYPE html>
<html lang="en">
<head>
<meta charset="utf-8">
<title>Verdant Build Calendar 2025 – May</title>
<link href="https://fonts.googleapis.com/css2?family=Roboto:wght@400;500;700&family=Open+Sans:wght@400;600;700&family=Oswald:wght@300;400&display=swap" rel="stylesheet">
<style>
  :root{
    --green:#22b064;
    --green-deep:#1b7a3c;
    --lime:#8dc63f;
    --weekend:#c9e4c0;
    --weekday:#ececec;
    --ink:#1f1f1f;
    --grey:#555555;
    --white:#ffffff;
  }
  *{margin:0;padding:0;box-sizing:border-box}
  html,body{width:785px;height:1200px;overflow:hidden;background:var(--white)}
  .calendar-page{position:relative;width:785px;height:1200px;background:var(--white);font-family:"Open Sans",sans-serif;color:var(--ink)}
  .hero{position:absolute;left:0;top:0}
  .brand{position:absolute;left:55px;top:88px}
  .brand-name{font-family:"Open Sans",sans-serif;font-weight:700;font-size:44px;letter-spacing:1px;color:var(--ink);line-height:1}
  .brand-tagline{font-family:"Open Sans",sans-serif;font-size:9.5px;color:var(--ink);margin-top:12px;letter-spacing:-.1px}
  .year-title{position:absolute;left:42px;top:590px;font-family:"Roboto",sans-serif}
  .year-title .label{font-size:32px;color:var(--green);font-weight:400;line-height:1;letter-spacing:-.5px}
  .year-title .year{font-size:72px;font-weight:700;line-height:1;letter-spacing:-3px;margin-top:-2px}
  .month-title{position:absolute;left:348px;top:640px;font-family:"Roboto",sans-serif;font-size:46px;color:var(--grey);font-weight:400}
  .month-grid{position:absolute;left:37px;top:706px;display:grid;grid-template-columns:repeat(7,67px);column-gap:4px;row-gap:9px;grid-template-rows:38px repeat(5,49px)}
  .month-grid .day-name{display:flex;align-items:center;justify-content:center;font-size:9px;font-weight:600;background:var(--weekday)}
  .month-grid .day-name.weekend{background:var(--weekend);color:var(--green-deep)}
  .month-grid .date{background:var(--weekday);font-family:"Roboto",sans-serif;font-weight:700;font-size:23px;display:flex;align-items:flex-end;padding:0 0 4px 4px}
  .month-grid .date.weekend{background:var(--weekend);color:var(--green-deep)}
  .month-grid .day-name,.month-grid .date{grid-row-end:span 1}
  .mini{position:absolute;left:568px;width:184px}
  .mini.april{top:702px}
  .mini.june{top:891px}
  .mini-head{display:flex;align-items:center;font-family:"Roboto",sans-serif;font-size:14px;margin-bottom:4px;padding-left:15px}
  .mini-head .m{width:56px;font-weight:500;letter-spacing:-.5px}
  .mini-head .y{color:var(--green);border-left:1.5px solid #aaa;padding-left:6px}
  .mini-grid{display:grid;grid-template-columns:repeat(7,25px);column-gap:1.5px;row-gap:4px;grid-template-rows:14px repeat(6,18px)}
  .mini-grid .day-name{font-size:3.6px;display:flex;align-items:center;justify-content:center;background:var(--weekday)}
  .mini-grid .day-name.weekend{background:var(--weekend);color:var(--green-deep)}
  .mini-grid .date{background:var(--weekday);font-size:8px;font-weight:600;display:flex;align-items:flex-end;padding:0 0 2px 4px}
  .mini-grid .date.weekend{background:var(--weekend);color:var(--green-deep)}
  .mini-grid .date.blank{background:transparent}
  .mini-grid .date.blank.weekend,.mini-grid .date.blank.fill{background:var(--weekday)}
  .mini-grid .date.blank.weekend{background:var(--weekend)}
  .footer{position:absolute;left:38px;top:1060px;display:flex;align-items:center;font-family:"Oswald",sans-serif;font-weight:300;font-size:11.5px;white-space:nowrap}
  .footer .brand-small{font-family:"Open Sans",sans-serif;font-weight:700;font-size:12px;width:80px}
  .footer .item{margin-right:15px}
  .footer .key{color:var(--green);font-weight:400}
</style>
</head>
<body>
<div class="calendar-page">
  <svg class="hero" width="785" height="640" viewBox="0 0 785 640">
    <defs>
      <linearGradient id="waveGreen" x1="0" y1="0" x2="1" y2="0">
        <stop offset="0" stop-color="#ffffff"/>
        <stop offset=".45" stop-color="#d7ecb6"/>
        <stop offset="1" stop-color="#8dc63f"/>
      </linearGradient>
      <linearGradient id="landscape" x1="0" y1="0" x2="0" y2="1">
        <stop offset="0" stop-color="#6f9a5a"/>
        <stop offset=".45" stop-color="#2f7a33"/>
        <stop offset=".8" stop-color="#3c7c32"/>
        <stop offset="1" stop-color="#b8683e"/>
      </linearGradient>
    </defs>
    <rect x="0" y="80" width="785" height="465" fill="url(#landscape)" role="img" aria-label="Aerial photo of a newly paved road forking through green plots and houses"/>
    <path d="M0,0 H785 V85 C600,78 380,140 0,190 Z" fill="url(#waveGreen)"/>
    <path d="M0,0 H785 V30 C560,40 330,10 0,60 Z" fill="#ffffff" opacity=".6"/>
    <path d="M0,530 C220,505 470,525 785,455 V625 C560,650 300,575 0,560 Z" fill="url(#waveGreen)"/>
    <path d="M0,560 C300,575 560,650 785,625 V640 H0 Z" fill="#ffffff"/>
  </svg>

  <div class="brand">
    <div class="brand-name">VERDANT BUILD</div>
    <div class="brand-tagline">VERDANT BUILD DEVELOPMENT</div>
  </div>

  <div class="year-title">
    <div class="label">CALENDAR</div>
    <div class="year">2025</div>
  </div>
  <div class="month-title">MAY</div>

  <div class="month-grid">
    <div class="day-name weekend">SUNDAY</div><div class="day-name">MONDAY</div><div class="day-name">TUESDAY</div><div class="day-name">WEDNESDAY</div><div class="day-name">THURSDAY</div><div class="day-name">FRIDAY</div><div class="day-name weekend">SATURDAY</div>
    <div class="date weekend"></div><div class="date"></div><div class="date"></div><div class="date"></div><div class="date">1</div><div class="date">2</div><div class="date weekend">3</div>
    <div class="date weekend">4</div><div class="date">5</div><div class="date">6</div><div class="date">7</div><div class="date">8</div><div class="date">9</div><div class="date weekend">10</div>
    <div class="date weekend">11</div><div class="date">12</div><div class="date">13</div><div class="date">14</div><div class="date">15</div><div class="date">16</div><div class="date weekend">17</div>
    <div class="date weekend">18</div><div class="date">19</div><div class="date">20</div><div class="date">21</div><div class="date">22</div><div class="date">23</div><div class="date weekend">24</div>
    <div class="date weekend">25</div><div class="date">26</div><div class="date">27</div><div class="date">28</div><div class="date">29</div><div class="date">30</div><div class="date weekend">31</div>
  </div>

  <div class="mini april">
    <div class="mini-head"><span class="m">APRIL</span><span class="y">2025</span></div>
    <div class="mini-grid">
      <div class="day-name weekend">SUNDAY</div><div class="day-name">MONDAY</div><div class="day-name">TUESDAY</div><div class="day-name">WEDNESDAY</div><div class="day-name">THURSDAY</div><div class="day-name">FRIDAY</div><div class="day-name weekend">SATURDAY</div>
      <div class="date blank weekend"></div><div class="date blank fill"></div><div class="date">1</div><div class="date">2</div><div class="date">3</div><div class="date">4</div><div class="date weekend">5</div>
      <div class="date weekend">6</div><div class="date">7</div><div class="date">8</div><div class="date">9</div><div class="date">10</div><div class="date">11</div><div class="date weekend">12</div>
      <div class="date weekend">13</div><div class="date">14</div><div class="date">15</div><div class="date">16</div><div class="date">17</div><div class="date">18</div><div class="date weekend">19</div>
      <div class="date weekend">20</div><div class="date">21</div><div class="date">22</div><div class="date">23</div><div class="date">24</div><div class="date">25</div><div class="date weekend">26</div>
      <div class="date weekend">27</div><div class="date">28</div><div class="date">29</div><div class="date">30</div><div class="date blank fill"></div><div class="date blank fill"></div><div class="date blank weekend"></div>
    </div>
  </div>

  <div class="mini june">
    <div class="mini-head"><span class="m">JUNE</span><span class="y">2025</span></div>
    <div class="mini-grid">
      <div class="day-name weekend">SUNDAY</div><div class="day-name">MONDAY</div><div class="day-name">TUESDAY</div><div class="day-name">WEDNESDAY</div><div class="day-name">THURSDAY</div><div class="day-name">FRIDAY</div><div class="day-name weekend">SATURDAY</div>
      <div class="date weekend">1</div><div class="date">2</div><div class="date">3</div><div class="date">4</div><div class="date">5</div><div class="date">6</div><div class="date weekend">7</div>
      <div class="date weekend">8</div><div class="date">9</div><div class="date">10</div><div class="date">11</div><div class="date">12</div><div class="date">13</div><div class="date weekend">14</div>
      <div class="date weekend">15</div><div class="date">16</div><div class="date">17</div><div class="date">18</div><div class="date">19</div><div class="date">20</div><div class="date weekend">21</div>
      <div class="date weekend">22</div><div class="date">23</div><div class="date">24</div><div class="date">25</div><div class="date">26</div><div class="date">27</div><div class="date weekend">28</div>
      <div class="date weekend">29</div><div class="date">30</div><div class="date blank fill"></div><div class="date blank fill"></div><div class="date blank fill"></div><div class="date blank fill"></div><div class="date blank weekend"></div>
    </div>
  </div>

  <div class="footer">
    <span class="brand-small">VERDANT</span>
    <span class="item"><span class="key">T</span>: +2348012345678</span>
    <span class="item"><span class="key">E</span>: hello@verdantbuild.com</span>
    <span class="item"><span class="key">W</span>: www.verdantbuild.com</span>
    <span class="item"><span class="key">A</span>: 22 Palm Grove Road, Garden Estate, Central District, Abuja Nigeria</span>
  </div>
</div>
</body>
</html>
```